Northvale Strategy Partners Website Design

I need a website design for my new business consulting and executive coaching firm, Northvale Strategy Partners. We provide consultative services to business C-suites as well as personal coaching to executives. I have attached the logo with color scheme I have chosen. I would like the website to reflect professionalism and continue the color scheme in the logo.

Target Market(s)

Small to medium business and their executives; middle to upper income men and women in mid- to late career looking for significance

Industry/Entity Type

Business Consultant

Number of Pages Required

4 page

Requirements
Must have
• A homepage with prominent logo and way to contact for more information; an area on the homepage with easy to read, clear text to describe what the company does; a prominent area on the homepage for a tagline; a blog page that can be updated regularly, an "about us" page with biographical information; an "about us" page; a page detailing services offered
• The web design must match the logo colors and font that I have uploaded.
Nice to have
• A lighthouse picture in the background or header
Should not have
• A lot of text area on the homepage

```html
<!DOCTYPE html>
<html lang="en">
<head>
<meta charset="utf-8">
<title>Northvale Strategy Partners</title>
<link href="https://fonts.googleapis.com/css2?family=Asap:wght@400;500;600&display=swap" rel="stylesheet">
<style>
:root{
  --navy:#1f2f5f;
  --wine:#6e1014;
  --ink:#555;
  --muted:#999;
  --line:#e3e3e3;
  --band:#f2f2f2;
  --band-dark:#ebebeb;
  --tri:#e6e6e6;
  --hero-top:#6d86b0;
  --hero-bottom:#a3a9b8;
  --photo-light:#d4d4d4;
  --photo-dark:#8a8a8a;
}
*{margin:0;padding:0;box-sizing:border-box}
html,body{width:705px;height:1200px;overflow:hidden;background:#fff}
body{position:relative;font-family:"Asap",sans-serif;color:var(--ink)}
.abs{position:absolute}
/* header */
.site-header{position:absolute;left:0;top:0;width:705px;height:72px;background:#fff}
.nav-link{position:absolute;top:31px;font-size:8.6px;color:#444;text-transform:uppercase;white-space:nowrap}
.nav-link.is-active{color:var(--navy);font-weight:500}
.nav-link.is-active::after{content:"";position:absolute;left:-4px;right:-4px;top:18px;height:2px;background:var(--wine)}
.brand{position:absolute;display:flex;align-items:center;gap:4px;white-space:nowrap}
.brand-mark{width:8px;height:8px;background:var(--navy);flex:none}
.brand-name{font-size:7.5px;font-weight:600;color:var(--navy);line-height:1.15;text-transform:uppercase;text-align:center;letter-spacing:.3px;white-space:nowrap}
.search-btn{position:absolute;left:588px;top:22px;width:31px;height:28px;background:var(--navy);color:#fff;font-size:5px;text-align:center;padding-top:6px}
/* hero */
.hero{position:absolute;left:0;top:72px;width:705px;height:258px;background:linear-gradient(180deg,var(--hero-top),var(--hero-bottom))}
.hero-title{position:absolute;left:0;width:705px;top:107px;text-align:center;color:#fff;font-size:26px;font-weight:400;letter-spacing:.3px;white-space:nowrap}
.hero-arrow{position:absolute;top:108px}
/* offer */
.section-title{position:absolute;left:0;width:705px;text-align:center;font-size:17.5px;color:#5a5a5a;font-weight:400;letter-spacing:.4px}
.offer{position:absolute;top:417px;width:180px;text-align:center}
.offer-icon{display:block;margin:0 auto}
.offer-name{margin-top:14px;font-size:8.6px;font-weight:500;color:var(--navy);text-transform:uppercase}
.offer-text{margin-top:14px;font-size:6.5px;line-height:1.7;color:var(--muted)}
.provide{position:absolute;left:0;top:594px;width:705px;height:316px;background:var(--band)}
.provide-text{position:absolute;top:838px;width:245px;font-size:6.5px;line-height:1.75;color:var(--muted)}
/* newsletter */
.newsletter{position:absolute;left:0;top:910px;width:705px;height:63px;background:var(--band-dark)}
.newsletter-label{position:absolute;left:125px;top:935px;font-size:9px;color:#333;text-transform:uppercase;white-space:nowrap}
.email-field{position:absolute;left:222px;top:928px;width:301px;height:26px;background:#fff;border:1px solid #ddd;font-size:5px;color:#aaa;padding:10px 9px;text-transform:uppercase}
.subscribe-btn{position:absolute;left:527px;top:928px;width:92px;height:26px;background:var(--wine);color:#fff;font-size:8.5px;text-align:center;line-height:26px;text-transform:uppercase}
/* footer */
.footer-rule{position:absolute;left:0;width:705px;height:1px;background:var(--line)}
.footer-brand{position:absolute;left:312px;top:988px;width:82px;height:34px;background:#fff;display:flex;align-items:center;justify-content:center;gap:3px}
.col-title{position:absolute;top:1047px;font-size:6.5px;font-weight:600;color:var(--navy);text-transform:uppercase}
.col-rule{position:absolute;top:1063px;height:1px;background:var(--line)}
.quick-links{position:absolute;left:85px;top:1070px;list-style:none;font-size:5.6px;color:#555;line-height:14px}
.col-body{position:absolute;font-size:5.6px;line-height:1.75;color:#555}
.news-date{color:var(--wine)}
.contact-row{position:absolute;left:450px;display:flex;gap:12px;font-size:5.6px;line-height:1.75;color:#555}
.copyright{position:absolute;left:85px;top:1179px;font-size:5.6px;color:#666}
.social{position:absolute;left:525px;top:1179px;display:flex;align-items:center;gap:4px;font-size:5.6px;color:#666}
.social-dot{width:5px;height:5px;background:#666;border-radius:50%}
</style>
</head>
<body>

<header class="site-header">
  <span class="nav-link is-active" style="left:131px">Home</span>
  <span class="nav-link" style="left:174px">About Us</span>
  <span class="nav-link" style="left:233px">Services</span>
  <div class="brand" style="left:312px;top:27px">
    <span class="brand-mark"></span>
    <span class="brand-name">Northvale<br>Strategy Partners</span>
  </div>
  <span class="nav-link" style="left:405px">Clients</span>
  <span class="nav-link" style="left:456px">Testimonials</span>
  <span class="nav-link" style="left:525px">Contact Us</span>
  <div class="search-btn">
    <svg width="8" height="8" viewBox="0 0 10 10"><circle cx="4" cy="4" r="3" fill="none" stroke="#fff" stroke-width="1.6"/><line x1="6.3" y1="6.3" x2="9" y2="9" stroke="#fff" stroke-width="1.8"/></svg>
    <div>SEARCH</div>
  </div>
</header>

<section class="hero" role="img" aria-label="Lighthouse on a rocky shore at sunset">
  <h1 class="hero-title">NORTHVALE STRATEGY PARTNERS</h1>
  <svg class="hero-arrow" style="left:0" width="37" height="43" viewBox="0 0 37 43"><polygon points="0,0 37,21.5 0,43" fill="var(--wine)"/><polyline points="14,16 9,21.5 14,27" fill="none" stroke="#fff" stroke-width="2"/></svg>
  <svg class="hero-arrow" style="left:668px" width="37" height="43" viewBox="0 0 37 43"><polygon points="37,0 0,21.5 37,43" fill="var(--wine)"/><polyline points="23,16 28,21.5 23,27" fill="none" stroke="#fff" stroke-width="2"/></svg>
</section>

<h2 class="section-title" style="top:367px">WHAT WE OFFER</h2>

<div class="offer" style="left:78px">
  <svg class="offer-icon" width="92" height="79" viewBox="0 0 92 79"><polygon points="46,0 92,79 0,79" fill="var(--tri)"/>
    <circle cx="46" cy="50" r="9" fill="none" stroke="var(--wine)" stroke-width="1.6"/><text x="46" y="54" text-anchor="middle" font-size="11" fill="var(--wine)" font-family="Asap,sans-serif">$</text></svg>
  <div class="offer-name">Financial Accounting</div>
  <p class="offer-text">Lorem Ipsum is simply dummy text of the printing and typesetting industry. Lorem Ipsum has been the industry's standard dummy text ever</p>
</div>
<div class="offer" style="left:262px">
  <svg class="offer-icon" width="92" height="79" viewBox="0 0 92 79"><polygon points="46,0 92,79 0,79" fill="var(--tri)"/>
    <polyline points="38,48 46,41 54,48" fill="none" stroke="var(--wine)" stroke-width="1.6"/><rect x="40" y="47" width="12" height="8" fill="none" stroke="var(--wine)" stroke-width="1.6"/><path d="M33,56 Q46,64 58,54" fill="none" stroke="var(--wine)" stroke-width="1.6"/></svg>
  <div class="offer-name">Property Protection</div>
  <p class="offer-text">Lorem Ipsum is simply dummy text of the printing and typesetting industry. Lorem Ipsum has been the industry's standard dummy text ever</p>
</div>
<div class="offer" style="left:445px">
  <svg class="offer-icon" width="92" height="79" viewBox="0 0 92 79"><polygon points="46,0 92,79 0,79" fill="var(--tri)"/>
    <rect x="39" y="40" width="13" height="17" fill="none" stroke="var(--wine)" stroke-width="1.6"/><line x1="42" y1="45" x2="49" y2="45" stroke="var(--wine)" stroke-width="1.2"/><line x1="42" y1="49" x2="47" y2="49" stroke="var(--wine)" stroke-width="1.2"/><circle cx="52" cy="56" r="4" fill="var(--tri)" stroke="var(--wine)" stroke-width="1.4"/></svg>
  <div class="offer-name">Tax and Regulatory</div>
  <p class="offer-text">Lorem Ipsum is simply dummy text of the printing and typesetting industry. Lorem Ipsum has been the industry's standard dummy text ever</p>
</div>

<section class="provide"></section>
<h2 class="section-title" style="top:626px">WHAT WE PROVIDE ?</h2>

<svg class="abs" style="left:0;top:670px" width="705" height="165" viewBox="0 670 705 165">
  <defs>
    <linearGradient id="greyPhoto" x1="0" y1="0" x2="0" y2="1"><stop offset="0" stop-color="var(--photo-light)"/><stop offset="1" stop-color="var(--photo-dark)"/></linearGradient>
  </defs>
  <polygon role="img" aria-label="Audience at a business conference" points="174,675 348,675 260,825" fill="url(#greyPhoto)"/>
  <polygon points="173,676 260,825 84,825" fill="var(--navy)"/>
  <text fill="#fff" font-family="Asap,sans-serif" font-size="14" text-anchor="middle"><tspan x="170" y="778">CONSULTATIVE</tspan><tspan x="170" y="795">SERVICES TO</tspan><tspan x="170" y="812">BUSINESS C-SUITES</tspan></text>
  <text x="352" y="752" fill="#666" font-family="Asap,sans-serif" font-size="16" text-anchor="middle">+</text>
  <polygon role="img" aria-label="Portrait of an executive" points="443,679 619,679 530,828" fill="url(#greyPhoto)"/>
  <polygon points="443,679 530,828 355,828" fill="var(--wine)"/>
  <text fill="#fff" font-family="Asap,sans-serif" font-size="14" text-anchor="middle"><tspan x="442" y="780">PERSONAL</tspan><tspan x="442" y="797">COACHING TO</tspan><tspan x="442" y="814">EXECUTIVES.</tspan></text>
</svg>
<p class="provide-text" style="left:85px">Lorem Ipsum is simply dummy text of the printing and typesetting industry. Lorem Ipsum has been the industry's standard dummy text ever since the 1500s, when an unknown printer took a galley of type and scrambled</p>
<p class="provide-text" style="left:353px">Lorem Ipsum is simply dummy text of the printing and typesetting industry. Lorem Ipsum has been the industry's standard dummy text ever since the 1500s, when an unknown printer took a galley of type and scrambled</p>

<section class="newsletter"></section>
<svg class="abs" style="left:102px;top:934px" width="17" height="13" viewBox="0 0 17 13"><rect x="1" y="1" width="15" height="11" rx="1.5" fill="none" stroke="var(--wine)" stroke-width="1.4"/><polyline points="1,2 8.5,8 16,2" fill="none" stroke="var(--wine)" stroke-width="1.4"/></svg>
<span class="newsletter-label">Newsletter Sign Up</span>
<div class="email-field">Enter your e-mail address</div>
<div class="subscribe-btn">Subscribe Now</div>

<footer>
  <div class="footer-rule" style="top:1004px"></div>
  <div class="footer-brand"><span class="brand-mark" style="width:6px;height:6px"></span><span class="brand-name" style="font-size:5.5px">Northvale<br>Strategy Partners</span></div>

  <span class="col-title" style="left:85px">Quick Links</span>
  <span class="col-rule" style="left:85px;width:67px"></span>
  <ul class="quick-links"><li>Home</li><li>About Us</li><li>Services</li><li>Clients</li><li>Testimonials</li><li>Contact Us</li></ul>

  <span class="col-title" style="left:175px">About Us</span>
  <span class="col-rule" style="left:175px;width:122px"></span>
  <p class="col-body" style="left:175px;top:1070px;width:122px">Lorem Ipsum is simply dummy text of the printing and typesetting industry. Lorem Ipsum has been the industry's standard dummy text ever since the 1500s</p>

  <span class="col-title" style="left:313px">News</span>
  <span class="col-rule" style="left:313px;width:122px"></span>
  <p class="col-body" style="left:314px;top:1069px;width:110px"><span class="news-date">December 30th, 2015</span><br><span style="display:block;margin-top:3px">Lorem Ipsum is simply dummy text of the printing and typesetting industry.</span></p>
  <p class="col-body" style="left:314px;top:1113px;width:110px"><span class="news-date">December 30th, 2015</span><br><span style="display:block;margin-top:3px">Lorem Ipsum is simply dummy text of the printing and typesetting industry.</span></p>

  <span class="col-title" style="left:450px">Contact Us</span>
  <span class="col-rule" style="left:450px;width:125px"></span>
  <div class="contact-row" style="top:1070px"><svg width="8" height="7" viewBox="0 0 8 7"><polygon points="4,0 8,2 0,2" fill="var(--wine)"/><rect x="1" y="2.5" width="1" height="3" fill="var(--wine)"/><rect x="3.5" y="2.5" width="1" height="3" fill="var(--wine)"/><rect x="6" y="2.5" width="1" height="3" fill="var(--wine)"/><rect x="0" y="6" width="8" height="1" fill="var(--wine)"/></svg><span>Harbor Desk<br>Kestrel Lane 42<br>20417 Lindmoor | Germany</span></div>
  <div class="contact-row" style="top:1109px"><svg width="8" height="7" viewBox="0 0 8 8"><path d="M1,1 L3,1 L4,3 L3,4 Q4,5.5 5,5 L6,4 L8,5 L8,7 Q3,8 1,1Z" fill="var(--wine)"/></svg><span>Telephone: +49 30 5550 1824</span></div>
  <div class="contact-row" style="top:1129px"><svg width="8" height="7" viewBox="0 0 8 7"><rect x=".5" y=".5" width="7" height="6" fill="none" stroke="var(--wine)"/><polyline points=".5,1 4,4 7.5,1" fill="none" stroke="var(--wine)"/></svg><span>E-mail: hello@northvale-example.com</span></div>

  <div class="footer-rule" style="top:1166px"></div>
  <span class="copyright">© 2015 Company Name | All Rights Reserved</span>
  <div class="social"><span>Connect With Us</span><span class="social-dot"></span><span class="social-dot"></span><span class="social-dot"></span><span class="social-dot"></span><span class="social-dot"></span></div>
</footer>

</body>
</html>
```